At Home Pet Euthanasia - business cards & brand stationary

We already have a logo and the colors and a website. Need a business card designed that will be able to customized to multiple veterinarians who will be partnering with us. The feel needs to be compassionate, comforting with our tagline 'A Gift of Love at Home'. It will be 2 sides.
On the back our platform/partner vets will be customizing each business card with their own service areas, phone numbers, name and title. On the front, i would like to see experimentation with use of our photos, the logo, tagline and a description 'Peaceful and Compassionate At-Home Pet Euthanasia'

```html
<!DOCTYPE html>
<html lang="en">
<head>
<meta charset="utf-8">
<title>Restful Paws – Business Card</title>
<link rel="stylesheet" href="https://fonts.googleapis.com/css2?family=Arimo:wght@400;700&display=swap">
<style>
  :root {
    --backdrop: #232323;
    --card: #0b0b0b;
    --brand-blue: #7b9cd2;
    --ink-white: #f2f2f2;
    --rule: #3a3a3a;
  }
  * { box-sizing: border-box; margin: 0; padding: 0; }
  html, body {
    width: 1200px; height: 900px; overflow: hidden;
    background: var(--backdrop);
    font-family: "Arimo", Arial, sans-serif;
  }
  .sheet {
    width: 1200px; height: 900px;
    display: flex; align-items: center; justify-content: center; gap: 40px;
  }
  .card {
    position: relative;
    width: 560px; height: 320px;
    background: var(--card);
    box-shadow: 0 12px 30px rgba(0,0,0,.55);
  }
  /* Contact side */
  .brand-name {
    color: var(--brand-blue); font-weight: 700;
    display: flex; align-items: center; gap: 10px;
    white-space: nowrap;
  }
  .brand-mark {
    width: 26px; height: 26px; border-radius: 50%;
    background: var(--brand-blue); flex: none;
  }
  .card--contact .brand-name {
    position: absolute; left: 34px; top: 140px; font-size: 27px;
  }
  .divider {
    position: absolute; left: 272px; top: 64px;
    width: 1px; height: 150px; background: var(--rule);
  }
  .details {
    position: absolute; left: 294px; top: 58px;
    color: var(--ink-white); font-size: 14px; line-height: 1.3;
  }
  .person-name {
    color: var(--brand-blue); font-weight: 700; font-size: 17px;
    text-transform: uppercase; letter-spacing: .5px;
  }
  .person-title { margin-bottom: 12px; }
  .contact-line { display: flex; align-items: center; gap: 8px; white-space: nowrap; }
  .contact-line svg { width: 14px; height: 14px; flex: none; }
  .highlight { color: var(--brand-blue); }
  .address { margin-top: 12px; }
  .service-line {
    position: absolute; left: 34px; right: 24px; bottom: 32px;
    color: var(--brand-blue); font-weight: 700; font-size: 13.5px;
    text-transform: uppercase; letter-spacing: .3px;
    white-space: nowrap;
  }
  /* Brand side */
  .card--brand { display: flex; align-items: center; justify-content: center; }
  .brand-lockup { text-align: left; }
  .card--brand .brand-name { font-size: 44px; gap: 14px; }
  .card--brand .brand-mark { width: 44px; height: 44px; }
  .tagline {
    color: var(--brand-blue); font-weight: 700; font-size: 14px;
    text-transform: uppercase; letter-spacing: .6px;
    margin-top: 8px; margin-left: 58px;
  }
</style>
</head>
<body>
<main class="sheet">
  <section class="card card--contact">
    <div class="brand-name"><span class="brand-mark"></span><span>Restful Paws</span></div>
    <div class="divider"></div>
    <div class="details">
      <p class="person-name">Daniel Harper</p>
      <p class="person-title">Managing Director</p>
      <p class="contact-line">
        <svg viewBox="0 0 24 24" fill="none" stroke="#f2f2f2" stroke-width="2"><path d="M5 3h4l2 5-2.5 1.5a11 11 0 0 0 6 6L16 13l5 2v4a2 2 0 0 1-2 2A16 16 0 0 1 3 5a2 2 0 0 1 2-2z"/></svg>
        <span>044-555 010 234</span>
      </p>
      <p class="contact-line">
        <svg viewBox="0 0 24 24" fill="none" stroke="#f2f2f2" stroke-width="2"><rect x="2" y="5" width="20" height="14"/><path d="M2 5l10 8 10-8"/></svg>
        <span>hello@restfulpaws.com</span>
      </p>
      <p class="contact-line">
        <svg viewBox="0 0 24 24" fill="none" stroke="#f2f2f2" stroke-width="2"><circle cx="12" cy="12" r="10"/><path d="M2 12h20M12 2a15 15 0 0 1 0 20M12 2a15 15 0 0 0 0 20"/></svg>
        <span>www.<span class="highlight">restfulpaws</span>.com</span>
      </p>
      <p class="address">421, Address line goes here<br>45452, Country Name</p>
    </div>
    <p class="service-line">Peaceful and compassionate at-home pet euthanasia</p>
  </section>

  <section class="card card--brand">
    <div class="brand-lockup">
      <div class="brand-name"><span class="brand-mark"></span><span>Restful Paws</span></div>
      <p class="tagline">A gift of love at home</p>
    </div>
  </section>
</main>
</body>
</html>
```